BOLD & MINIMALIST DESIGN NEEDED

We want a very bold but minimalistic business card design that is impactful and utilizes both sides of the business card. Our current logo is included for your use.

We want bold fonts and good use of negative space. We don't want the logo to overpower the design.

Target Market(s)

Professionals who are building new commercial buildings.

Industry/Entity Type

Construction

Contact Information for Business Card

Name, Title, email, office phone, cell phone, website

Font styles to use
Serif
Sans Serif

Requirements
Must have
• Bold design!

```html
<!DOCTYPE html>
<html lang="en">
<head>
<meta charset="utf-8">
<title>Ridgemont Business Card</title>
<link href="https://fonts.googleapis.com/css2?family=Montserrat:wght@400;600;800&display=swap" rel="stylesheet">
<style>
  :root {
    --backdrop: #949494;
    --paper: #ffffff;
    --ink: #0b0c0e;
    --green: #8dc956;
    --light: #ffffff;
    --rule: #55585c;
  }
  * { margin: 0; padding: 0; box-sizing: border-box; }
  html, body { width: 1200px; height: 1200px; overflow: hidden; }
  body {
    background: var(--backdrop);
    font-family: "Montserrat", sans-serif;
    position: relative;
  }
  .card {
    position: absolute;
    left: 179px;
    width: 861px;
    height: 496px;
    background: var(--paper);
    overflow: hidden;
  }
  .card--front { top: 84px; }
  .card--back { top: 621px; }

  .brand {
    position: absolute;
    left: 0; right: 0;
    display: flex;
    align-items: center;
    justify-content: center;
    gap: 16px;
    color: var(--ink);
    font-weight: 800;
    letter-spacing: 1px;
    line-height: 1;
  }
  .card--front .brand { top: 216px; font-size: 56px; }
  .brand__mark { width: 34px; height: 34px; background: var(--green); }
  .card--back .brand { top: 36px; font-size: 62px; }

  .band { position: absolute; left: 0; top: 0; width: 861px; height: 496px; }

  .person {
    position: absolute;
    right: 392px;
    top: 352px;
    text-align: right;
  }
  .person__name { color: var(--light); font-weight: 600; font-size: 35px; line-height: 1; }
  .person__title { color: var(--green); font-weight: 400; font-size: 28px; line-height: 1; margin-top: 10px; }

  .divider {
    position: absolute;
    left: 481px; top: 339px;
    width: 1px; height: 121px;
    background: var(--rule);
  }
  .contacts {
    position: absolute;
    left: 492px; top: 330px;
    list-style: none;
  }
  .contacts li {
    display: flex;
    align-items: center;
    height: 34px;
    color: var(--light);
    font-size: 23px;
    letter-spacing: 0.5px;
  }
  .contacts svg { width: 26px; height: 26px; margin-right: 14px; flex: none; }
  .accent { color: var(--green); }
</style>
</head>
<body>
  <section class="card card--front">
    <div class="brand"><span class="brand__mark"></span>RIDGEMONT</div>
  </section>

  <section class="card card--back">
    <div class="brand">RIDGEMONT</div>

    <svg class="band" viewBox="0 0 861 496" aria-hidden="true">
      <path d="M0 298 H343 Q430 274 518 298 H861 V496 H0 Z" fill="var(--ink)"/>
      <path d="M0 297 H343 Q430 273 518 297 H861" fill="none" stroke="var(--green)" stroke-width="3"/>
    </svg>

    <div class="person">
      <div class="person__name">Name Surename</div>
      <div class="person__title">Director</div>
    </div>

    <div class="divider"></div>

    <ul class="contacts">
      <li>
        <svg viewBox="0 0 24 24"><path d="M6.6 3.5l3 3.2-1.8 2.2a12 12 0 006.3 6.3l2.2-1.8 3.2 3-1.6 3.1C10 19.2 4.8 14 4 5.1z" fill="var(--green)"/><path d="M14 3a7 7 0 017 7M14 6.5a3.5 3.5 0 013.5 3.5" fill="none" stroke="var(--green)" stroke-width="1.8"/></svg>
        555-014-2200
      </li>
      <li>
        <svg viewBox="0 0 24 24"><path d="M2 9c0-3 20-3 20 0v2h-5V9H7v2H2z" fill="var(--green)"/><path d="M6 12h12l2 8H4z" fill="var(--green)"/><circle cx="12" cy="16" r="2.2" fill="var(--ink)"/></svg>
        555-014-2200
      </li>
      <li>
        <svg viewBox="0 0 24 24"><rect x="2" y="5" width="20" height="14" fill="var(--green)"/><path d="M2 5l10 8 10-8M2 19l7-7M22 19l-7-7" fill="none" stroke="var(--ink)" stroke-width="1.5"/></svg>
        info@r-m-b.com
      </li>
      <li>
        <svg viewBox="0 0 24 24" fill="none" stroke="var(--green)" stroke-width="1.6"><circle cx="12" cy="12" r="10"/><ellipse cx="12" cy="12" rx="4.5" ry="10"/><path d="M2 12h20M4 7h16M4 17h16M12 2v20"/></svg>
        www.<span class="accent">r-m-b</span>.com
      </li>
    </ul>
  </section>
</body>
</html>
```